KBT Business Cards

We require business cards for our business. We would like a matte black back to the card, with our logo centred in the middle. The front side of the card is open to design.

Target Market(s)

Clients looking for legal services (professional)

Industry/Entity Type

Legal

Contact Information for Business Card

Doran Kelbrath
Partner
Mobile: 0461 738 524
Email: doran@kbtlaw.co
Website: www.kbtlaw.co
Level 3, 118 Wendmore Street
Sydney NSW 2000

Font styles to use
Other font styles liked:
• Avenir

Colors
f04a50
ffffff
1b1b1b

Requirements
Must have
• Black back with logo included in the centre of the card.
• Our font is Avenir.

```html
<!DOCTYPE html>
<html lang="en">
<head>
<meta charset="utf-8">
<title>KBT Business Cards</title>
<link rel="stylesheet" href="https://fonts.googleapis.com/css2?family=Nunito+Sans:wght@400;600;700&display=swap">
<style>
  :root {
    --ink: #1b1b1b;
    --accent: #f04a50;
    --paper: #ffffff;
    --paper-soft: #f2f2f2;
    --stage: #d9d9d9;
    --muted: #bfbfbf;
  }
  * { margin: 0; padding: 0; box-sizing: border-box; }
  html, body {
    width: 1200px; height: 675px; overflow: hidden;
    background: var(--stage);
    font-family: "Nunito Sans", "Avenir", sans-serif;
  }
  .sheet { position: relative; width: 1200px; height: 675px; }

  .card {
    position: absolute; top: 195px;
    width: 500px; height: 286px;
    overflow: hidden;
    box-shadow: 0 6px 18px rgba(0,0,0,0.18);
  }
  .card--front { left: 70px; background: var(--paper-soft); }
  .card--back { left: 630px; background: var(--ink); }

  .card__shape { position: absolute; inset: 0; width: 100%; height: 100%; }

  .holder {
    position: absolute; top: 88px; right: 26px;
    color: var(--paper); font-size: 14px; letter-spacing: 0.3px;
    white-space: nowrap;
  }
  .holder__name { font-weight: 600; text-transform: uppercase; }
  .holder__role { font-weight: 400; padding-left: 6px; margin-left: 4px; border-left: 1.5px solid var(--paper); }

  .contact {
    position: absolute; left: 32px; top: 142px;
    color: var(--ink); font-size: 13.5px; line-height: 19px;
    font-style: normal;
  }
  .contact__line { display: flex; align-items: center; gap: 8px; }
  .contact__icon { width: 11px; height: 11px; flex: none; }
  .contact__web-domain { color: var(--accent); font-weight: 700; }
  .contact__address { display: block; margin-top: 8px; font-size: 14px; line-height: 18px; }

  .mark {
    position: absolute; display: flex; align-items: center; gap: 9px;
    color: var(--paper); font-weight: 700; letter-spacing: 1px;
  }
  .mark__square { background: var(--accent); flex: none; }
  .mark--front { right: 58px; bottom: 46px; font-size: 22px; }
  .mark--front .mark__square { width: 18px; height: 18px; }

  .mark--back {
    left: 50%; top: 50%; transform: translate(-50%, -60%);
    font-size: 17px; line-height: 21px; gap: 14px;
  }
  .mark--back .mark__square { width: 34px; height: 34px; }

  .back__web {
    position: absolute; bottom: 22px; left: 0; right: 0; text-align: center;
    color: var(--muted); font-size: 11px; letter-spacing: 0.6px;
  }
</style>
</head>
<body>
<main class="sheet">

  <section class="card card--front" aria-label="Business card front">
    <svg class="card__shape" viewBox="0 0 500 286" preserveAspectRatio="none" aria-hidden="true">
      <path d="M160,0 L500,0 L500,286 L385,286 C340,190 250,70 160,0 Z" fill="var(--ink)"/>
      <path d="M268,150 C305,190 330,240 348,286 L362,286 C340,230 310,185 268,150 Z" fill="var(--ink)"/>
    </svg>

    <p class="holder"><span class="holder__name">Doran Kelbrath</span><span class="holder__role">Partner</span></p>

    <address class="contact">
      <span class="contact__line">
        <svg class="contact__icon" viewBox="0 0 12 12" aria-hidden="true"><path d="M2.5,1 L4.5,1 L5.3,3.5 L4,4.5 C4.7,6 6,7.3 7.5,8 L8.5,6.7 L11,7.5 L11,9.5 C11,10.3 10.3,11 9.5,11 C5,11 1,7 1,2.5 C1,1.7 1.7,1 2.5,1 Z" fill="var(--accent)"/></svg>
        0461 738 524
      </span>
      <span class="contact__line">
        <svg class="contact__icon" viewBox="0 0 12 12" aria-hidden="true"><rect x="1" y="2.5" width="10" height="7" fill="none" stroke="var(--accent)" stroke-width="1.3"/><path d="M1,2.5 L6,6.5 L11,2.5" fill="none" stroke="var(--accent)" stroke-width="1.3"/></svg>
        doran@kbtlaw.co
      </span>
      <span class="contact__line">
        <svg class="contact__icon" viewBox="0 0 12 12" aria-hidden="true"><circle cx="6" cy="6" r="5" fill="none" stroke="var(--accent)" stroke-width="1.2"/><ellipse cx="6" cy="6" rx="2.2" ry="5" fill="none" stroke="var(--accent)" stroke-width="1"/><path d="M1,6 L11,6" stroke="var(--accent)" stroke-width="1"/></svg>
        <span>www.<span class="contact__web-domain">kbtlaw</span>.co</span>
      </span>
      <span class="contact__address">Level 3, 118 Wendmore Street<br>Sydney NSW 2000</span>
    </address>

    <div class="mark mark--front"><span class="mark__square"></span><span class="mark__name">KBT</span></div>
  </section>

  <section class="card card--back" aria-label="Business card back">
    <div class="mark mark--back">
      <span class="mark__square"></span>
      <span class="mark__name">KELBRATH<br>BOWDEN<br>TARRANT</span>
    </div>
    <p class="back__web">www.kbtlaw.co</p>
  </section>

</main>
</body>
</html>
```